Company Website for Varnoth Signal, an open source data analytics company focused on relationship and li

I need a company/brand website for our new startup, Varnoth Signal LLC. We are a company focused on using life pattern analysis techniques, looking at relationships and how relationships, attributes, and activity cluster to infer aggregate information about individuals and groups. Our focus is on improving the digital advertising market.

We have a company logo which I will upload shortly.

Target Market(s)

Digital Advertising

Number of Pages Required

3 page

Font styles to use
Sans Serif

Requirements
Must have
• An main page, about us, contact page.
Nice to have
• Varnoth Signal relies on state of the art analytics applied to a the digital marketing space. While it is heavy in science, we also understand the art of influence. The website should have a scientific edge but also a flair that illustrates our focus on applying the hard science and analytics to influencing the behavior of people.

```html
<!DOCTYPE html>
<html lang="en">
<head>
<meta charset="utf-8">
<title>Varnoth Signal – Data Analytics</title>
<link href="https://fonts.googleapis.com/css2?family=Poppins:wght@400;500;600&family=Open+Sans:wght@400;600;700&display=swap" rel="stylesheet">
<style>
:root{
  --navy:#0a1a3d;
  --navy-deep:#050d24;
  --blue:#1e88e5;
  --blue-bright:#2196f3;
  --orange:#f68b1f;
  --orange-deep:#e4620c;
  --ink:#1d1d1d;
  --text:#333;
  --muted:#555;
  --light:#f2f3f5;
  --white:#fff;
  --black:#0b0b0b;
  --line:#9a9a9a;
}
*{box-sizing:border-box;margin:0;padding:0}
html,body{width:1200px;height:3482px;overflow:hidden}
body{position:relative;background:var(--white);font-family:"Open Sans",Arial,sans-serif;color:var(--text)}
section,header,footer{position:absolute;left:0;width:1200px}
.abs{position:absolute}
.btn{position:absolute;display:flex;align-items:center;justify-content:center;background:var(--orange);color:var(--white);font-family:"Poppins",Arial,sans-serif;font-weight:500;border-radius:40px;text-transform:uppercase;letter-spacing:.5px}

/* hero */
.hero{top:0;height:685px;background:radial-gradient(ellipse at 50% 70%,#1f4aa8 0%,#10296b 35%,var(--navy) 65%,var(--navy-deep) 100%);overflow:hidden}
.hero-waves{position:absolute;left:0;top:380px;width:1200px;height:305px;background:linear-gradient(180deg,rgba(40,110,230,0) 0%,rgba(50,130,240,.35) 50%,rgba(20,60,160,.2) 100%)}
.menu{left:77px;top:56px;width:40px}
.menu span{display:block;height:5px;background:var(--white);margin-bottom:7px;border-radius:2px}
.menu span:nth-child(2){width:30px}
.brand{left:0;width:1200px;top:40px;text-align:center;font-family:"Poppins",Arial,sans-serif;font-weight:600;font-size:34px;color:var(--blue-bright)}
.phone{right:78px;top:50px;display:flex;align-items:center;gap:12px;color:var(--white);font-family:"Poppins",Arial,sans-serif;font-size:23px}
.hero h1{left:0;width:1200px;top:245px;text-align:center;font-family:"Poppins",Arial,sans-serif;font-weight:500;font-size:86px;color:var(--white);letter-spacing:1px}
.hero-sub{left:0;width:1200px;top:348px;text-align:center;font-family:"Poppins",Arial,sans-serif;font-size:30px;color:var(--white)}
.hero .btn{left:503px;top:427px;width:195px;height:56px;font-size:22px}
.arrow{top:350px}

/* welcome */
.welcome{top:685px;height:580px;background:var(--white)}
.welcome-square{left:78px;top:105px;width:148px;height:130px;background:var(--blue)}
.laptop{left:58px;top:130px;width:522px;height:300px}
.welcome h2{left:603px;top:148px;font-family:"Poppins",Arial,sans-serif;font-weight:400;font-size:38px;color:var(--ink)}
.welcome h2 em,.services h2 em,.analytics h2 em{font-style:normal;color:var(--blue)}
.welcome p{left:606px;top:200px;width:514px;font-size:13px;line-height:24px;text-align:justify}
.welcome .btn{left:606px;top:362px;width:124px;height:33px;font-size:13px}

/* services */
.services{top:1265px;height:627px;background:var(--light);overflow:hidden}
.services-blue{left:759px;top:0;width:441px;height:627px;background:var(--blue)}
.services h2{left:86px;top:100px;font-family:"Poppins",Arial,sans-serif;font-weight:500;font-size:38px;line-height:48px;color:var(--ink)}
.services h2 em{color:var(--orange)}
.services p{left:86px;width:332px;font-size:13px;line-height:24px;text-align:justify}
.services .btn{left:86px;top:483px;width:127px;height:36px;font-size:13px}
.service-card{left:471px;top:81px;width:652px;height:476px;background:var(--white);box-shadow:0 4px 20px rgba(0,0,0,.12)}
.service{position:absolute;width:250px;text-align:center}
.service .icon{width:72px;height:72px;margin:0 auto;border-radius:50%;background:var(--orange);border:5px solid #fbd3a8;display:flex;align-items:center;justify-content:center}
.service h3{margin-top:14px;font-size:12.5px;font-weight:700;color:var(--ink);letter-spacing:.5px}
.service p{position:static;width:auto;margin-top:6px;font-size:12.5px;line-height:18px;text-align:center;color:var(--muted)}

/* analytics */
.analytics{top:1892px;height:696px;background:var(--white)}
.analytics h2{left:0;width:1200px;top:113px;text-align:center;font-family:"Poppins",Arial,sans-serif;font-weight:500;font-size:40px;color:var(--ink)}
.post{top:215px;width:488px;height:377px;background:var(--white);box-shadow:0 3px 14px rgba(0,0,0,.16)}
.post .media{height:219px}
.post h3{margin:28px 0 0 30px;font-family:"Poppins",Arial,sans-serif;font-weight:400;font-size:21px;color:var(--ink)}
.post p{margin:10px 30px 0;font-size:12.5px;line-height:21px;color:var(--muted)}
.post a{display:inline-block;margin:10px 0 0 30px;font-size:11px;color:var(--orange);text-decoration:none;border-bottom:2px solid var(--orange);padding-bottom:4px}

/* touch */
.touch{top:2588px;height:285px;background:linear-gradient(100deg,var(--orange-deep) 0%,var(--orange) 45%,#ef7a1a 70%,var(--orange-deep) 100%)}
.touch h2{left:0;width:1200px;top:62px;text-align:center;font-family:"Poppins",Arial,sans-serif;font-weight:500;font-size:40px;color:var(--white)}
.socials{left:289px;top:143px;display:flex;gap:31px}
.socials span{width:62px;height:62px;border:3px solid var(--white);border-radius:50%}

/* contact */
.contact{top:2873px;height:485px;background:var(--white)}
.contact h3{font-size:19px;font-weight:600;color:var(--ink);top:93px}
.info-item{left:123px;display:flex;gap:40px}
.info-item .label{font-size:15px;color:var(--ink);line-height:21px}
.info-item .label span{display:block;color:var(--text)}
.field{left:592px;width:485px;height:41px;border:2px solid var(--line);padding:9px 12px;font-size:15px;color:var(--ink)}
.contact .btn{left:965px;top:404px;width:112px;height:28px;font-size:14px}

/* footer */
.site-footer{top:3358px;height:124px;background:var(--black);color:#bbb;font-size:13px;text-align:center;line-height:124px}
</style>
</head>
<body>

<header class="hero">
  <div class="hero-waves" role="img" aria-label="Glowing blue digital particle wave landscape"></div>
  <div class="abs menu" aria-label="Menu"><span></span><span></span><span></span></div>
  <div class="abs brand">Varnoth Signal</div>
  <div class="abs phone">
    <svg width="26" height="26" viewBox="0 0 24 24" fill="none" stroke="#f68b1f" stroke-width="2"><circle cx="12" cy="12" r="10.5"/><path d="M8.5 7.5l1.6-.3 1 2.2-1 .9a6 6 0 0 0 2.6 2.6l.9-1 2.2 1-.3 1.6c-3.5.6-7.6-3.5-7-7z" fill="#f68b1f" stroke="none"/></svg>
    5550142876
  </div>
  <h1 class="abs">DATA ANALYTICS</h1>
  <div class="abs hero-sub">Focused on relationship and lifestyle behaviors</div>
  <div class="btn">View More</div>
  <svg class="abs arrow" style="left:63px" width="14" height="24" viewBox="0 0 14 24"><path d="M11 3L3 12l8 9" fill="none" stroke="#fff" stroke-width="2"/></svg>
  <svg class="abs arrow" style="left:1122px" width="14" height="24" viewBox="0 0 14 24"><path d="M3 3l8 9-8 9" fill="none" stroke="#fff" stroke-width="2"/></svg>
</header>

<section class="welcome">
  <div class="abs welcome-square"></div>
  <div class="abs laptop" role="img" aria-label="Laptop showing a big data chart" style="background:linear-gradient(160deg,#2b2b2b 0%,#4a4a4a 100%);border-radius:10px 10px 4px 4px;padding:14px">
    <div style="width:100%;height:100%;background:linear-gradient(180deg,#eef6f7 0%,#bfe3e3 55%,#2aa8a6 100%)"></div>
  </div>
  <h2 class="abs"><em>Welcome to</em> Varnoth Signal</h2>
  <p class="abs">It is a long established fact that a reader will be distracted by the readable content of a page when looking at its layout. The point of using Lorem Ipsum is that it has a more-or-less normal distribution of letters, as opposed to using 'Content here, content here', making it look like readable English. Many desktop publishing packages and web page editors now use Lorem Ipsum as their default model text, and a search for 'lorem ipsum' will uncover many web sites still in their infancy.</p>
  <div class="btn">Read More</div>
</section>

<section class="services">
  <div class="abs services-blue"></div>
  <h2 class="abs"><em>Our</em><br>Services</h2>
  <p class="abs" style="top:213px">It is a long established fact that a reader will be distracted by the readable content of a page when looking at its layout. The point of using Lorem Ipsum is that it has a more-or-less normal distribution of letters, as opposed to using 'Content here, content here',</p>
  <p class="abs" style="top:345px">Making it look like readable English. Many desktop publishing packages and web page editors now use Lorem Ipsum as their default model text, and a search for 'lorem ipsum' will uncover many web sites still in their infancy various versions have evolved.</p>
  <div class="btn">Read More</div>
  <div class="abs service-card">
    <div class="service" style="left:56px;top:44px">
      <div class="icon"><svg width="30" height="30" viewBox="0 0 24 24" fill="none" stroke="#fff" stroke-width="1.6"><rect x="3" y="4" width="18" height="12" rx="1"/><path d="M9 20h6M12 16v4M6 12l4-4 3 3 4-4"/></svg></div>
      <h3>NEQUE PORRO QUISQUAM</h3>
      <p>Lorem ipsum dolor sit amet, consectetur adipiscing elit, sed do e.iusmod tempor incididunt</p>
    </div>
    <div class="service" style="left:342px;top:44px">
      <div class="icon"><svg width="30" height="30" viewBox="0 0 24 24" fill="none" stroke="#fff" stroke-width="1.6"><circle cx="10" cy="10" r="6"/><path d="M14.5 14.5L20 20M7.5 10l2 2 3-4"/></svg></div>
      <h3>DOLOREM IPSUM QUIA</h3>
      <p>Lorem ipsum dolor sit amet, consectetur adipiscing elit, sed do e.iusmod tempor incididunt</p>
    </div>
    <div class="service" style="left:56px;top:260px">
      <div class="icon"><svg width="30" height="30" viewBox="0 0 24 24" fill="none" stroke="#fff" stroke-width="1.6"><circle cx="12" cy="7" r="3"/><path d="M6 20v-3a6 6 0 0 1 12 0v3M4 12h3M17 12h3"/></svg></div>
      <h3>IPSUM QUIA DOLOR</h3>
      <p>Lorem ipsum dolor sit amet, consectetur adipiscing elit, sed do e.iusmod tempor incididunt</p>
    </div>
    <div class="service" style="left:342px;top:260px">
      <div class="icon"><svg width="30" height="30" viewBox="0 0 24 24" fill="none" stroke="#fff" stroke-width="1.6"><path d="M6 3h9l4 4v14H6z"/><path d="M9 10h7M9 13h7M9 16h5"/></svg></div>
      <h3>PORRO QUISQUAM EST</h3>
      <p>Lorem ipsum dolor sit amet, consectetur adipiscing elit, sed do e.iusmod tempor incididunt</p>
    </div>
  </div>
</section>

<section class="analytics">
  <h2 class="abs"><em>Data</em> Analytics</h2>
  <article class="abs post" style="left:93px">
    <div class="media" role="img" aria-label="Group of young people sitting together using phones and a laptop" style="background:linear-gradient(135deg,#5a5550 0%,#8a7f74 50%,#3c3935 100%)"></div>
    <h3>Neque porro quisquam</h3>
    <p>The point of using Lorem Ipsum is that it has a more-or-less normal distribution of letters, as opposed to using 'Content here, content here',</p>
    <a href="#">READ MORE</a>
  </article>
  <article class="abs post" style="left:615px">
    <div class="media" role="img" aria-label="Laptop on a desk with blue digital data overlay" style="background:linear-gradient(135deg,#1b3f7a 0%,#5f8ec4 50%,#c9d8ea 100%)"></div>
    <h3>Dolorem ipsum quia dolor</h3>
    <p>The point of using Lorem Ipsum is that it has a more-or-less normal distribution of letters, as opposed to using 'Content here, content here',</p>
    <a href="#">READ MORE</a>
  </article>
</section>

<section class="touch" role="img" aria-label="Orange-toned photo of hands working on a laptop">
  <h2 class="abs">Get in Touch</h2>
  <div class="abs socials" aria-label="Social links"><span></span><span></span><span></span><span></span><span></span><span></span><span></span></div>
</section>

<section class="contact">
  <h3 class="abs" style="left:123px">CONTACT US</h3>
  <div class="abs info-item" style="top:160px">
    <svg width="46" height="34" viewBox="0 0 46 34" fill="none" stroke="#1e88e5" stroke-width="2"><rect x="2" y="2" width="42" height="30" rx="2"/><path d="M2 3l21 16L44 3"/></svg>
    <div class="label">Email<span>hello@varnothsignal.example</span></div>
  </div>
  <div class="abs info-item" style="top:240px">
    <svg width="46" height="50" viewBox="0 0 46 50" fill="none" stroke="#1e88e5" stroke-width="2"><rect x="11" y="2" width="24" height="46" rx="3"/><path d="M11 10h24M11 40h24"/><circle cx="23" cy="44" r="1.5"/></svg>
    <div class="label">Call Us !<span>+1 555 014 2210</span><span>+1 555 014 2210</span></div>
  </div>
  <div class="abs info-item" style="top:348px">
    <svg width="46" height="50" viewBox="0 0 46 50" fill="none" stroke="#1e88e5" stroke-width="2"><path d="M23 46S9 30 9 19a14 14 0 0 1 28 0c0 11-14 27-14 27z"/><circle cx="23" cy="19" r="5"/><path d="M4 46h38"/></svg>
    <div class="label">Address<span>48 Lantern Row, Eastfield,</span><span>Northland 204118</span></div>
  </div>
  <h3 class="abs" style="left:590px">CONTACT FORM</h3>
  <div class="abs field" style="top:154px">Name</div>
  <div class="abs field" style="top:205px">Email</div>
  <div class="abs field" style="top:256px">Phone</div>
  <div class="abs field" style="top:307px;height:86px">Message</div>
  <div class="btn">Submit</div>
</section>

<footer class="site-footer">© 2018 Company Name. All right reserved</footer>

</body>
</html>
```